Vantro cards

I am in the auto motive, transportation business I would like a business card that is Something cool, modern edgy, having to do with car culture. I offer towing service for high and exotic cars. I also provide towing for collisions and car accidents. I offer open and enclosed transport nationwide.

Target Market(s)

Car culture people high end auto collectors

Industry/Entity Type

Towing car carrier

Contact Information for Business Card

My company colors black yellow and silver

Font styles to use
Serif

```html
<!DOCTYPE html>
<html lang="en">
<head>
<meta charset="utf-8">
<title>Vantro business cards</title>
<link href="https://fonts.googleapis.com/css2?family=Arimo:wght@400;700&display=swap" rel="stylesheet">
<style>
  :root {
    --bg: #d9d9d6;
    --card: #1f1f1f;
    --card-deep: #171717;
    --yellow: #f5dc4c;
    --silver: #b4b4b6;
    --white: #f2f2f2;
    --mark-faint: #141414;
  }
  * { margin: 0; padding: 0; box-sizing: border-box; }
  html, body { width: 1200px; height: 801px; overflow: hidden; }
  body {
    background: var(--bg);
    font-family: "Arimo", Arial, sans-serif;
    display: flex;
    align-items: center;
    justify-content: center;
    gap: 40px;
  }
  .card {
    position: relative;
    width: 540px;
    height: 309px;
    background: var(--card);
    border: 3px solid var(--yellow);
    overflow: hidden;
  }
  .brand {
    position: absolute;
    top: 48px;
    right: 48px;
    display: flex;
    align-items: center;
    gap: 14px;
  }
  .brand-square {
    width: 22px;
    height: 22px;
    background: var(--yellow);
  }
  .brand-name {
    font-weight: 700;
    font-size: 48px;
    letter-spacing: 3px;
    color: var(--silver);
  }
  .edge-tab {
    position: absolute;
    left: 0;
    top: 150px;
    width: 16px;
    height: 26px;
    background: var(--yellow);
  }
  .person {
    position: absolute;
    left: 40px;
    top: 142px;
  }
  .person-name {
    font-weight: 700;
    font-size: 22px;
    letter-spacing: 0.5px;
    color: var(--yellow);
    text-transform: uppercase;
  }
  .person-role {
    font-size: 14px;
    color: var(--white);
    margin-top: 2px;
  }
  .contact {
    position: absolute;
    left: 150px;
    top: 196px;
    list-style: none;
    font-size: 13px;
    line-height: 16px;
    color: var(--white);
  }
  .contact li { display: flex; align-items: center; gap: 8px; }
  .contact .plain { padding-left: 20px; }
  .contact svg { width: 12px; height: 12px; flex: none; }
  .back-mark {
    position: absolute;
    inset: 0;
    display: flex;
    align-items: center;
    justify-content: center;
    font-weight: 700;
    font-size: 64px;
    letter-spacing: 4px;
    color: var(--mark-faint);
  }
</style>
</head>
<body>
  <section class="card card-front">
    <div class="brand">
      <span class="brand-square"></span>
      <span class="brand-name">VANTRO</span>
    </div>
    <span class="edge-tab"></span>
    <div class="person">
      <p class="person-name">Darren Holt</p>
      <p class="person-role">CEO/Founder</p>
    </div>
    <ul class="contact">
      <li class="plain">P.O. Box 3870 Road</li>
      <li class="plain">Region Name CD 4127</li>
      <li>
        <svg viewBox="0 0 12 12"><path d="M2.5 1 L4.5 1 L5.2 3.6 L4 4.6 Q5 7 7.4 8 L8.4 6.8 L11 7.5 L11 9.5 Q10.5 11 9 11 Q1 10 1 2.5 Q1 1.2 2.5 1Z" fill="var(--yellow)"/></svg>
        (555) 201 4470
      </li>
      <li>
        <svg viewBox="0 0 12 12"><rect x="3" y="0.8" width="6" height="10.4" rx="1" fill="none" stroke="var(--yellow)" stroke-width="1.4"/><circle cx="6" cy="9.2" r="0.7" fill="var(--yellow)"/></svg>
        (555) 318 9062
      </li>
      <li>
        <svg viewBox="0 0 12 12"><rect x="0.5" y="2.5" width="11" height="7.5" fill="var(--yellow)"/><path d="M0.5 2.5 L6 7 L11.5 2.5" fill="none" stroke="var(--card)" stroke-width="1"/></svg>
        hello@vantrohaul.com
      </li>
      <li>
        <svg viewBox="0 0 12 12"><circle cx="6" cy="6" r="5.2" fill="none" stroke="var(--yellow)" stroke-width="1.2"/><ellipse cx="6" cy="6" rx="2.2" ry="5.2" fill="none" stroke="var(--yellow)" stroke-width="1"/><path d="M0.8 6 H11.2 M1.8 3.4 H10.2 M1.8 8.6 H10.2" stroke="var(--yellow)" stroke-width="0.9"/></svg>
        www.vantrohaul.com
      </li>
    </ul>
  </section>

  <section class="card card-back">
    <div class="back-mark">VANTRO</div>
  </section>
</body>
</html>
```